Trailer wrap for home remodeling company in Sarasota County Florida

I need a wrap design for an enclosed trailer. I like the idea of adding a picture of a really nice kitchen or bathroom, possibly a before and after.
Matte black background
Must include the below information
Pinecrest Home Remodeling
CGC2871093
941-555–0184
www.pinecresthomeremodeling.example
Bathrooms,Kitchens, Additions, Remodels
Trusted Expertise. Refined Design
Trailer is currently all black
Updates

Designs are not what we are looking for, very busy

Industry/Entity Type

Home Remodeling

Colors
0054AA
0677BA
7BADD7
CADEEF
E8F1F8

Requirements
Must have
• Matte black background

```html
<!DOCTYPE html>
<html lang="en">
<head>
<meta charset="utf-8">
<title>Pinecrest Home Remodeling — Trailer Wrap</title>
<link rel="stylesheet" href="https://fonts.googleapis.com/css2?family=Montserrat:ital,wght@0,500;0,700;0,800;1,800&display=swap">
<style>
  :root {
    --matte-black: #0b0b0c;
    --charcoal: #3a3b3e;
    --navy: #0054aa;
    --ocean: #0677ba;
    --sky: #2fa9e6;
    --powder: #7badd7;
    --mist: #cadeef;
    --frost: #e8f1f8;
    --panel: #eef0f2;
    --ink: #141414;
    --white: #ffffff;
  }
  * { margin: 0; padding: 0; box-sizing: border-box; }
  html, body { width: 1200px; height: 616px; overflow: hidden; background: var(--white); }
  .wrap {
    position: relative; width: 1200px; height: 616px; overflow: hidden;
    font-family: "Montserrat", Arial, sans-serif;
    background: linear-gradient(180deg, var(--panel) 0%, #e4e7ea 60%, #d3e6f2 100%);
  }
  .shapes { position: absolute; inset: 0; }
  .service-photos {
    position: absolute; top: 0; right: 0; width: 260px; height: 616px;
    background:
      linear-gradient(90deg, var(--panel) 0%, rgba(238,240,242,0) 45%),
      linear-gradient(180deg, #d9dcdf 0%, #c9b9a6 30%, #d7d2cc 48%, #e6e2dc 70%, var(--powder) 88%, var(--sky) 100%);
  }
  .brand {
    position: absolute; left: 52px; top: 48px; color: var(--white);
    font-weight: 500; text-transform: uppercase; letter-spacing: 6px; line-height: 1;
  }
  .brand-name { font-size: 46px; }
  .brand-sub { font-size: 24px; letter-spacing: 14px; margin-top: 14px; padding-left: 4px; }
  .tagline {
    position: absolute; left: 52px; top: 166px; color: var(--white);
    font-weight: 800; font-size: 44px; line-height: 48px; text-transform: uppercase;
  }
  .tagline em { font-style: italic; color: var(--sky); }
  .license {
    position: absolute; left: 20px; top: 276px; color: var(--white);
    font-weight: 700; font-size: 22px;
  }
  .phone {
    position: absolute; left: 54px; top: 346px; color: var(--white);
    font-weight: 800; font-size: 62px; letter-spacing: 1px;
  }
  .website {
    position: absolute; left: 54px; top: 440px; color: var(--white);
    font-weight: 700; font-size: 25px;
  }
  .services { position: absolute; left: 860px; top: 0; width: 200px; list-style: none; }
  .services li {
    position: absolute; left: 0; width: 200px; text-align: center;
    font-weight: 700; font-size: 24px; color: var(--ink);
  }
  .services li:nth-child(1) { top: 88px; }
  .services li:nth-child(2) { top: 221px; }
  .services li:nth-child(3) { top: 353px; }
  .services li:nth-child(4) { top: 485px; }
</style>
</head>
<body>
<div class="wrap">
  <div class="service-photos" role="img" aria-label="Photos of a finished bathroom, a modern kitchen and a hand drafting remodel plans"></div>

  <svg class="shapes" width="1200" height="616" viewBox="0 0 1200 616" aria-hidden="true">
    <defs>
      <linearGradient id="phone-band" x1="0" x2="1" y1="0" y2="0">
        <stop offset="0" stop-color="#29b4ee"/>
        <stop offset="0.55" stop-color="var(--ocean)"/>
        <stop offset="1" stop-color="var(--navy)"/>
      </linearGradient>
      <linearGradient id="lower-field" x1="0" x2="1" y1="0" y2="1">
        <stop offset="0" stop-color="#8f9297"/>
        <stop offset="0.5" stop-color="#c9ccd0"/>
        <stop offset="1" stop-color="var(--sky)"/>
      </linearGradient>
    </defs>
    <!-- lower gradient field -->
    <polygon points="0,470 660,470 600,616 0,616" fill="url(#lower-field)"/>
    <!-- matte black field -->
    <polygon points="0,0 700,0 580,330 0,330" fill="var(--matte-black)"/>
    <!-- diagonal accent stripes -->
    <polygon points="700,0 770,0 650,330 580,330" fill="var(--navy)"/>
    <polygon points="770,0 790,0 670,330 650,330" fill="var(--ocean)"/>
    <polygon points="690,160 730,160 660,330 620,330" fill="var(--sky)" opacity="0.8"/>
    <!-- license bar -->
    <polygon points="0,272 362,272 344,312 0,312" fill="var(--charcoal)"/>
    <polygon points="368,272 392,272 374,312 350,312" fill="var(--sky)"/>
    <!-- white rule -->
    <rect x="0" y="324" width="650" height="4" fill="var(--white)"/>
    <!-- phone band -->
    <polygon points="0,333 710,333 672,432 0,432" fill="url(#phone-band)"/>
    <!-- website band -->
    <polygon points="0,432 672,432 652,478 0,478" fill="#3c3d40"/>
    <!-- service separators -->
    <g stroke="#b8bcc2" stroke-width="1.5">
      <line x1="850" y1="165" x2="1070" y2="165"/>
      <line x1="850" y1="298" x2="1070" y2="298"/>
      <line x1="850" y1="430" x2="1070" y2="430"/>
    </g>
  </svg>

  <div class="brand">
    <div class="brand-name">Pinecrest Home</div>
    <div class="brand-sub">Remodeling</div>
  </div>

  <h1 class="tagline">Trusted <em>Expertise</em><br>Refined <em>Design</em></h1>
  <p class="license">License # CGC2871093</p>
  <p class="phone">941-555–0184</p>
  <p class="website">www.pinecresthomeremodeling.example</p>

  <ul class="services">
    <li>Bathrooms</li>
    <li>Kitchens</li>
    <li>Additions</li>
    <li>Remodels</li>
  </ul>
</div>
</body>
</html>
```